We need 5-10 Instagram posts for a restaurant located in Dubai, UAE.

Background about the restaurant:

Forks and fizz is a boutique burgers and comfort food joint located at Dubai, UAE. We started operations in September 2016. The main focus on our food is for it to be simple, original and freshly made. The majority of our orders are take away with fewer people opting for dinning in. We connect with our customers through our Instagram account & our customers rely on it for updates.

The brief

What we are looking for is a vector design (advertisement) for multiple purposes including:

1. announcing that we started delivery
2. a post that we can use multiple times during the year just as a "reminder that we deliver"
3. posts that serve as an advertisement

posts need to be as simple as possible

for reference, our Instagram account is @forksandfizz

Colors
f04a50
ffffff
000000

Requirements
Should not have
• the designs should not have too many colors

```html
<!DOCTYPE html>
<html lang="en">
<head>
<meta charset="utf-8">
<title>Forks and fizz — delivery posts</title>
<link rel="stylesheet" href="https://fonts.googleapis.com/css2?family=Montserrat:wght@700&display=swap">
<style>
  :root {
    --backdrop: #d8d8d8;
    --post-bg: #ffffff;
    --brand-red: #ee2a2a;
    --ink: #1e1e1e;
  }
  * { margin: 0; padding: 0; box-sizing: border-box; }
  html, body {
    width: 1200px;
    height: 1200px;
    overflow: hidden;
    background: var(--backdrop);
  }
  .post-row {
    position: absolute;
    top: 330px;
    left: 40px;
    display: flex;
    gap: 40px;
  }
  .post {
    width: 540px;
    height: 540px;
    background: var(--post-bg);
    box-shadow: 0 10px 24px rgba(0,0,0,0.18);
    display: flex;
    flex-direction: column;
    align-items: center;
    padding-top: 96px;
  }
  .post-icon {
    display: block;
    width: 150px;
    height: 120px;
    border-radius: 10px;
    background: linear-gradient(135deg, #3a3a3a, #111111);
    margin-bottom: 22px;
  }
  .post-icon--burger { width: 190px; height: 96px; margin-bottom: 30px; margin-top: 12px; }
  .post-icon--finger { width: 110px; height: 124px; }
  .headline {
    font-family: "Montserrat", sans-serif;
    font-weight: 700;
    font-size: 76px;
    line-height: 84px;
    text-align: center;
    letter-spacing: -1px;
  }
  .headline__accent { display: block; color: var(--brand-red); }
  .headline__main { display: block; color: var(--ink); }
</style>
</head>
<body>
  <main class="post-row">
    <article class="post post--announce">
      <div class="post-icon post-icon--burger" role="img" aria-label="Black stamped burger icon speeding to the right with motion lines"></div>
      <h1 class="headline">
        <span class="headline__accent">we started</span>
        <span class="headline__main">delivery</span>
      </h1>
    </article>
    <article class="post post--reminder">
      <div class="post-icon post-icon--finger" role="img" aria-label="Black stamped hand icon with a string tied around the raised index finger as a reminder"></div>
      <h1 class="headline">
        <span class="headline__accent">we delivery</span>
        <span class="headline__main">to you</span>
      </h1>
    </article>
  </main>
</body>
</html>
```